Neues Etikett für Wasch- und Reinigungspaste
Zielgruppe
KAVIMOR, das sind wir, Spezialisten in Hygiene und Gastronomiebedarf. Wir stellen Reinigungsmittel im oberösterreichischen Mühlviertel (Aigen-Schlägl) her und wir beraten, planen und bieten die komplette Einrichtung von Gastronomieküchen an.
Unsere Hygieneprodukte tragen dazu bei, dass sich Menschen in einem Gebäude wohl fühlen. Denn Sauberkeit und Hygiene sind Faktoren, die für unsere Gesundheit wichtig sind. Die Zielgruppen im Bereich Reinigungsmittel sind Eigenheimbesitzer, Wohnraum-Mieter und in Betrieben das Reinigungspersonal bzw. die verantworlichen Mitarbeiter für die Objekthygiene.
Aufgabenstellung
Kurz: Wir suchen für ein altes Produkt ein neues Etikett. Das Produkt heißt „Rutosan“ und ist eine Wasch- und Reinigungspaste / Schmierseife, also ein altbewährtes Hausmittel, dass auch heute noch wunderbar vielseitig einsetzbar ist. Wir möchten ihr Image gerne etwas aufpeppen, da es unserer Meinung nach im Allgemeinen und auch bei uns zu stiefmütterlich auftritt. Wir denken, dass sie mehr in den Mittelpunkt rücken sollte, gerade da sie in vielen Fällen andere Reinigungsmittel ersetzen kann und auch durch ihre Ergiebigkeit die Umwelt entlastet.
Wir haben uns bewusst dazu entschieden, das alte Etikett hier nicht mit hochzuladen, daß heißt hier soll es keinen Wiedererkennungswert zu anderen Kavimor-Produkten geben. Bitte orientieren Sie sich allein an diesem Briefing.
Das Produkt ist sehr nachhaltig, ergiebig und damit sparsam. Erhältlich ist es in einem weißen, runden 5 kg Eimer (siehe Upload). Das Endformat des Etiketts auf dem weissen Eimer beträgt maximal 150 mm (H) x 170 mm (B). Es ist auch in kleineren und größeren Einheiten erhältlich, jedoch wird das Etikett dann durch uns angepasst.
Es ist wichtig, dass auf den ersten Blick sichtbar ist, dass es sich um eine Wasch- und Reinigungspaste handelt. Sie reinigt zum Beispiel Geschirr, Besteck, Aluminium, Glas, lackierte Möbel, Kunststoffmöbel, Fliesen, Waschbecken, Badewannen, Fahrzeuge, Maschinen, schmierige Hände, Holz- und Kunststoffböden, Feinwäsche, Wolle, Seide, Vorhänge, zum Einweichen und Vorwaschen von Arbeits- und Buntwäsche. Anwendung: 1 Esslöffel auf 10 Liter Wasser oder auch pur anwendbar je nach Einsatzbereich. Enthält keine Phosphate und ist biologisch abbaubar. Inhalt: 5 kg

```html
<!DOCTYPE html>
<html lang="de">
<head>
<meta charset="utf-8">
<title>Rutosan Schmierseife – Etikett</title>
<link rel="stylesheet" href="https://fonts.googleapis.com/css2?family=Archivo+Black&family=Bebas+Neue&family=Roboto+Condensed:wght@400;700&display=swap">
<style>
  :root {
    --tile-blue: #86dcf6;
    --grout: #5fc4e8;
    --signal-red: #e5182b;
    --navy: #0f2b3a;
    --white: #ffffff;
    --page: #ffffff;
  }
  * { margin: 0; padding: 0; box-sizing: border-box; }
  html, body {
    width: 1200px; height: 701px; overflow: hidden;
    background: var(--page);
  }
  .label {
    position: absolute; left: 295px; top: 4px;
    width: 610px; height: 692px; overflow: hidden;
    background-color: var(--tile-blue);
    background-image:
      linear-gradient(90deg, var(--grout) 3px, transparent 3px),
      linear-gradient(180deg, var(--grout) 3px, transparent 3px);
    background-size: 104px 104px;
    background-position: 42px 0, 0 -8px;
    box-shadow: 0 10px 30px rgba(0,0,0,.18);
    font-family: "Roboto Condensed", sans-serif;
    color: var(--navy);
  }
  .waves { position: absolute; inset: 0; }
  .brand {
    position: absolute; left: 0; right: 0; top: 40px;
    text-align: center;
  }
  .brand-name {
    display: inline-flex; align-items: center; gap: 8px;
    font-family: "Roboto Condensed", sans-serif; font-weight: 700;
    font-size: 26px; letter-spacing: 1px; color: var(--navy);
  }
  .brand-dot { width: 14px; height: 14px; border-radius: 50%; background: var(--signal-red); }
  .brand-tagline { font-size: 10px; color: var(--navy); margin-top: 2px; }
  .content-size {
    position: absolute; right: 36px; top: 22px; text-align: center;
    font-family: "Bebas Neue", sans-serif; color: var(--navy); line-height: 1;
  }
  .content-size .caption { font-size: 22px; }
  .content-size .amount { font-size: 32px; }
  .product-name {
    position: absolute; left: 0; right: 0; top: 130px; text-align: center;
    font-family: "Archivo Black", sans-serif; font-size: 92px; line-height: 1;
    color: var(--signal-red); letter-spacing: -1px;
    text-shadow: 4px 5px 0 var(--navy);
  }
  .product-type {
    position: absolute; left: 0; right: 0; top: 245px; text-align: center;
    font-family: "Bebas Neue", sans-serif; font-size: 54px; letter-spacing: 5px;
    color: var(--navy); line-height: 1;
  }
  .claims { position: absolute; left: 218px; top: 318px; list-style: none; }
  .claims li {
    display: flex; align-items: center; gap: 8px;
    font-size: 21px; height: 38px;
  }
  .claims svg { width: 30px; height: 28px; }
  .usage { position: absolute; left: 12px; top: 453px; }
  .section-title {
    font-family: "Roboto Condensed", sans-serif; font-weight: 700;
    color: var(--signal-red); font-size: 21px; text-transform: uppercase;
    letter-spacing: -.3px; margin-bottom: 6px;
  }
  .usage p { font-size: 16px; line-height: 24px; letter-spacing: -.3px; }
  .applications { position: absolute; left: 12px; right: 12px; top: 566px; color: var(--white); }
  .applications p { font-size: 16px; line-height: 24.5px; letter-spacing: -.35px; }
</style>
</head>
<body>
  <main class="label">
    <svg class="waves" viewBox="0 0 610 692" aria-hidden="true">
      <path d="M0 432 C120 425 250 440 380 462 C470 478 540 480 610 468 L610 692 L0 692Z" fill="var(--white)"/>
      <circle cx="559" cy="478" r="18" fill="var(--white)"/>
      <circle cx="528" cy="485" r="10" fill="var(--white)"/>
      <circle cx="584" cy="474" r="8" fill="var(--white)"/>
      <path d="M0 548 C150 560 300 580 420 575 C500 570 560 545 610 520 L610 692 L0 692Z" fill="var(--navy)"/>
      <circle cx="417" cy="572" r="18" fill="var(--navy)"/>
      <circle cx="447" cy="577" r="8" fill="var(--navy)"/>
      <circle cx="489" cy="573" r="6" fill="var(--navy)"/>
    </svg>

    <header class="brand">
      <div class="brand-name"><span class="brand-dot"></span>KAVIMOR</div>
      <div class="brand-tagline">Betriebshygiene | Gastronomieservice</div>
    </header>

    <div class="content-size">
      <div class="caption">Inhalt</div>
      <div class="amount">5 kg</div>
    </div>

    <h1 class="product-name">RUTOSAN</h1>
    <h2 class="product-type">Schmierseife</h2>

    <ul class="claims">
      <li><svg viewBox="0 0 30 28"><path d="M4 15 L11 22 L27 4" fill="none" stroke="var(--navy)" stroke-width="6" stroke-linecap="round" stroke-linejoin="round" transform="translate(2 2)"/><path d="M4 15 L11 22 L27 4" fill="none" stroke="var(--signal-red)" stroke-width="5" stroke-linecap="round" stroke-linejoin="round"/></svg>Phosphatfrei</li>
      <li><svg viewBox="0 0 30 28"><path d="M4 15 L11 22 L27 4" fill="none" stroke="var(--navy)" stroke-width="6" stroke-linecap="round" stroke-linejoin="round" transform="translate(2 2)"/><path d="M4 15 L11 22 L27 4" fill="none" stroke="var(--signal-red)" stroke-width="5" stroke-linecap="round" stroke-linejoin="round"/></svg>Biologisch abbaubar</li>
    </ul>

    <section class="usage">
      <h3 class="section-title">Anwendung:</h3>
      <p>1 Esslöffel auf 10 Liter Wasser.<br>Auch pur anwendbar je nach Einsatzbereich.</p>
    </section>

    <section class="applications">
      <h3 class="section-title">Vielseitig einsetzbar!</h3>
      <p>Für Geschirr, Besteck, Aluminium, Glas, lackierte Möbel, Kunststoffmöbel, Fliesen, Waschbecken, Badewannen, Fahrzeuge, Maschinen, schmierige Hände, Holz- und Kunststoffböden, Feinwäsche, Wolle, Seide, Vorhänge, zum Einweichen und Vorwaschen von Arbeits- und Buntwäsche.</p>
    </section>
  </main>
</body>
</html>
```